The most modern business card ever !!!

Our company call “Vendalo”. Vendalo is a technology company specialized in cruises solutions. Out main product is a platform to reserve cruises. This is a revolutionary platform that make easier to travel agencies and final users to reserve cruises across dozen companies like tibba, wernu, hpv, dgb, etc..We are a “start up”, with a young team of developers and we want to transmit it.. For it, we want something different, a modern business card that represent cruises and technology.. When someone receive this card, this person should say: wowww this is different… this is modern… this is a cruise related company..
- diferent, modern
- traditions business card

```html
<!DOCTYPE html>
<html lang="en">
<head>
<meta charset="utf-8">
<title>Vendalo Business Card</title>
<link href="https://fonts.googleapis.com/css2?family=Montserrat:wght@400;500;600&display=swap" rel="stylesheet">
<style>
  :root {
    --page-bg: #8a8a8a;
    --card-white: #ffffff;
    --card-black: #161616;
    --ink: #1a1a1a;
    --accent: #2aa3dc;
    --emboss: #3c3c3c;
  }
  * { margin: 0; padding: 0; box-sizing: border-box; }
  html, body {
    width: 1200px; height: 900px; overflow: hidden;
    background: var(--page-bg);
    font-family: "Montserrat", sans-serif;
  }
  .stage {
    width: 1200px; height: 900px;
    display: flex; flex-direction: column;
    align-items: center; justify-content: center; gap: 60px;
  }
  .card {
    width: 620px; height: 354px;
    position: relative;
    box-shadow: 0 6px 18px rgba(0,0,0,0.25);
  }
  .card--front { background: var(--card-white); }
  .card--back {
    background: var(--card-black);
    display: flex; align-items: center; justify-content: center;
  }
  .brand {
    position: absolute; left: 52px; top: 130px;
    display: flex; align-items: center; gap: 10px;
  }
  .brand__mark { width: 16px; height: 16px; background: var(--accent); }
  .brand__name {
    font-size: 44px; font-weight: 500; color: var(--ink);
    letter-spacing: 1px;
  }
  .contact {
    position: absolute; left: 360px; top: 78px;
    color: var(--ink);
  }
  .contact__name {
    font-size: 17px; font-weight: 600; color: var(--accent);
    letter-spacing: 0.5px; text-transform: uppercase;
  }
  .contact__role { font-size: 11px; margin-top: 2px; margin-left: 8px; }
  .contact__address {
    font-size: 11px; line-height: 1.45; margin-top: 18px; margin-left: 16px;
    letter-spacing: 0.5px;
  }
  .contact__list {
    list-style: none; margin-top: 16px; margin-left: 28px;
    font-size: 11px; line-height: 1.65; letter-spacing: 0.5px;
  }
  .contact__list li { display: flex; align-items: center; gap: 8px; }
  .contact__list svg { width: 9px; height: 9px; flex: none; }
  .accent { color: var(--accent); }
  .back-name {
    font-size: 78px; font-weight: 500; color: var(--emboss);
    letter-spacing: 2px;
  }
</style>
</head>
<body>
<main class="stage">
  <section class="card card--front">
    <div class="brand">
      <span class="brand__mark"></span>
      <span class="brand__name">Vendalo</span>
    </div>
    <div class="contact">
      <p class="contact__name">Daniel Harrow</p>
      <p class="contact__role">Director</p>
      <p class="contact__address">214b Marlow Street,<br>Hillcrest, NZ, 4120</p>
      <ul class="contact__list">
        <li>
          <svg viewBox="0 0 10 10" aria-hidden="true"><path d="M2 1 L4 1 L4.6 3 L3.5 3.8 Q4.5 5.8 6.2 6.5 L7 5.4 L9 6 L9 8 Q5 9 2.5 6 Q1 4 2 1 Z" fill="var(--accent)"/></svg>
          (555) 201-7748
        </li>
        <li>
          <svg viewBox="0 0 10 10" aria-hidden="true"><rect x="1" y="2" width="8" height="6" fill="none" stroke="var(--accent)"/><path d="M1 2 L5 5.5 L9 2" fill="none" stroke="var(--accent)"/></svg>
          info@vendalo.com.br
        </li>
        <li>
          <svg viewBox="0 0 10 10" aria-hidden="true"><circle cx="5" cy="5" r="4" fill="none" stroke="var(--accent)"/><path d="M1 5 H9 M5 1 V9" stroke="var(--accent)" stroke-width="0.8"/></svg>
          <span>www.<span class="accent">vendalo</span>.com.br</span>
        </li>
      </ul>
    </div>
  </section>
  <section class="card card--back">
    <span class="back-name">Vendalo</span>
  </section>
</main>
</body>
</html>
```